TALMORK

The business want a professional looking business card. We have a scetch we will add but want the extra upgrade, and would like more suggestions for variations of our business cards.

```html
<!DOCTYPE html>
<html lang="en">
<head>
<meta charset="utf-8">
<title>Talmork Business Card</title>
<link href="https://fonts.googleapis.com/css2?family=Cinzel:wght@500;700&family=Outfit:wght@400&display=swap" rel="stylesheet">
<style>
  :root {
    --backdrop: #f2f1ef;
    --card-light: #f4efe6;
    --card-dark: #e5d5b9;
    --ink-brown: #6a4320;
    --gold: #b38d45;
    --gold-soft: #c7a566;
  }
  * { margin: 0; padding: 0; box-sizing: border-box; }
  html, body {
    width: 1200px; height: 702px; overflow: hidden;
    background: var(--backdrop);
  }
  .canvas { position: relative; width: 1200px; height: 702px; }
  .card {
    position: absolute; top: 175px; height: 349px;
    background: linear-gradient(125deg, var(--card-light) 0%, #efe6d7 50%, var(--card-dark) 100%);
  }
  .card--front { left: 67px; width: 523px; }
  .card--back { left: 632px; width: 508px; }

  .company-title {
    position: absolute; left: 45px; top: 40px;
    font-family: "Cinzel", serif; font-weight: 700;
    font-size: 35px; letter-spacing: 0.5px; color: var(--ink-brown);
    white-space: nowrap;
  }
  .role {
    position: absolute; left: 45px; top: 88px;
    font-family: "Outfit", sans-serif; font-size: 31px; color: var(--ink-brown);
  }
  .person-name {
    position: absolute; left: 45px; top: 126px;
    font-family: "Outfit", sans-serif; font-size: 22px; color: var(--ink-brown);
  }
  .contact-list { position: absolute; left: 45px; top: 212px; list-style: none; }
  .contact-item {
    display: flex; align-items: center; height: 36px; margin-bottom: 0;
    font-family: "Outfit", sans-serif; font-size: 23px; color: var(--ink-brown);
  }
  .contact-icon { width: 23px; height: 24px; margin-right: 16px; flex: none; }
  .brand-lockup {
    position: absolute; left: 388px; top: 232px; width: 110px;
    display: flex; flex-direction: column; align-items: center;
  }
  .brand-dot { width: 30px; height: 30px; border-radius: 50%; background: var(--gold); margin-bottom: 12px; }
  .brand-name {
    font-family: "Cinzel", serif; font-weight: 500; font-size: 16px;
    letter-spacing: 3px; color: var(--gold);
  }
  .brand-since {
    font-family: "Outfit", sans-serif; font-size: 6px; letter-spacing: 2px;
    color: var(--gold); margin-top: 3px;
  }
  .back-lockup {
    position: absolute; left: 0; right: 0; top: 80px;
    display: flex; flex-direction: column; align-items: center;
  }
  .back-dot { width: 96px; height: 96px; border-radius: 50%; background: var(--gold); margin-bottom: 36px; }
  .back-name {
    font-family: "Cinzel", serif; font-weight: 500; font-size: 36px;
    letter-spacing: 10px; color: var(--gold); padding-left: 10px;
  }
  .back-since {
    font-family: "Outfit", sans-serif; font-size: 11px; letter-spacing: 5px;
    color: var(--ink-brown); opacity: 0.8; margin-top: 8px; padding-left: 5px;
  }
</style>
</head>
<body>
<main class="canvas">
  <section class="card card--front">
    <h1 class="company-title">TALMORK SOLBERGA</h1>
    <p class="role">CEO &amp; Founder</p>
    <p class="person-name">Aksel Varden Solberga</p>
    <ul class="contact-list">
      <li class="contact-item">
        <svg class="contact-icon" viewBox="0 0 24 24" aria-hidden="true">
          <rect x="6" y="1" width="12" height="22" rx="2" fill="none" stroke="#6a4320" stroke-width="2.2"/>
          <circle cx="12" cy="19.5" r="1.2" fill="#6a4320"/>
        </svg>
        004791234560
      </li>
      <li class="contact-item">
        <svg class="contact-icon" viewBox="0 0 24 24" aria-hidden="true">
          <rect x="1" y="5" width="22" height="15" fill="#6a4320"/>
          <path d="M1 5 L12 14 L23 5 M1 20 L9 12 M23 20 L15 12" fill="none" stroke="#efe6d7" stroke-width="1.4"/>
        </svg>
        talmork.llc@mailhub.com
      </li>
      <li class="contact-item">
        <svg class="contact-icon" viewBox="0 0 24 24" aria-hidden="true">
          <circle cx="12" cy="12" r="10.5" fill="none" stroke="#6a4320" stroke-width="1.6"/>
          <ellipse cx="12" cy="12" rx="4.5" ry="10.5" fill="none" stroke="#6a4320" stroke-width="1.2"/>
          <path d="M1.5 12 H22.5 M3.5 7 H20.5 M3.5 17 H20.5" stroke="#6a4320" stroke-width="1.2"/>
        </svg>
        www.talmork.llc
      </li>
    </ul>
    <div class="brand-lockup">
      <span class="brand-dot"></span>
      <span class="brand-name">TALMORK</span>
      <span class="brand-since">SINCE 2026</span>
    </div>
  </section>

  <section class="card card--back">
    <div class="back-lockup">
      <span class="back-dot"></span>
      <span class="back-name">TALMORK</span>
      <span class="back-since">SINCE 2026</span>
    </div>
  </section>
</main>
</body>
</html>
```